Online tuition webpage design needed

Hi,
We are starting up an online tuition website for non- English speakers wishing to take an TOVAR test.

The webpage must include a place for people to enroll online in the course.
The home page must have:
• room for a logo (coming shortly, blue in colour)
• different packages of online tuition and paywick
• tool bar showing different pages
• perhaps a video, small pictures

This is my site currently:-

www.lexavotutoring.com

as you can see, I am not very sure how to create a website … The large logo is what I would like to use, but I project has not been finalized yet. Please note, I don’t like the logo being that large!

Sites that are similar to what I am doing and like the design of are:

http://www.brindacourse.com.au/fees

https://www.quorvel9x.net/index.php

http://www.lessonmasterpercival.co.uk/index.html

http://www.tamrunexamhub.com/

One thing I need is a place for student s to enroll, and if possible, I would like to use learnix to create exercises for students.
Currently, my site is using sitecraft. My preference is to use learnix for online activities. I am not sure if I can use both.
Thanks in advance

Target Market(s)

people wising to take an TOVAR test (English proficiency test)

Industry/Entity Type

Online

Colors
3276b5
0292cd

Requirements
Must have
• a place for enrollment and admin login for students
learnix
video
voxly, friendbook, chirpnet logos
Nice to have
• a booking calender
Should not have
• too much clutter. must be clean and professional looking

```html
<!DOCTYPE html>
<html lang="en">
<head>
<meta charset="utf-8">
<title>TOVAR Online Tuition</title>
<link href="https://fonts.googleapis.com/css2?family=Open+Sans:wght@300;400;600;700&display=swap" rel="stylesheet">
<style>
:root{
  --brand:#1f4ea3;
  --blue:#3276b5;
  --nav-top:#3b82c4;
  --nav-bottom:#1d5c9e;
  --nav-active:#164b84;
  --footer:#1d5591;
  --orange:#f7941d;
  --diamond:#f26a0a;
  --text:#666;
  --heading:#555;
  --line:#e3e3e3;
  --cal-head:#1f5fa3;
  --cal-days:#3278bd;
}
*{box-sizing:border-box;margin:0;padding:0}
html,body{width:963px;height:1200px;overflow:hidden;background:#fff}
body{font-family:"Open Sans",Arial,sans-serif;color:var(--text);position:relative}
.topline{position:absolute;top:0;left:0;width:963px;height:3px;background:#e6e6e6}

.logo{position:absolute;left:52px;top:16px;display:flex;align-items:center;gap:8px}
.logo-mark{width:36px;height:36px;background:var(--brand);border-radius:50%}
.logo-name{font-size:34px;font-weight:400;color:var(--brand);line-height:1}
.logo-sub{position:absolute;left:120px;top:62px;font-size:14px;color:var(--brand);white-space:nowrap}

.social{position:absolute;top:11px;left:660px;display:flex;gap:8px;font-size:10px;font-weight:600;color:var(--blue)}
.enroll{position:absolute;top:3px;left:806px;width:105px;height:29px;background:var(--orange);color:#fff;font-size:14px;font-weight:600;text-align:center;line-height:28px}
.login{position:absolute;top:53px;left:614px;display:flex;gap:4px}
.login .field{width:124px;height:23px;border:1px solid #d5d5d5;border-radius:3px;font-size:10px;color:#999;padding:4px 8px}
.login .btn{width:50px;height:23px;margin-left:4px;background:linear-gradient(#3b82c4,#1d5c9e);border-radius:3px;color:#fff;font-size:11px;font-weight:600;text-align:center;line-height:22px}

.nav{position:absolute;top:90px;left:0;width:963px;height:43px;background:linear-gradient(var(--nav-top),var(--nav-bottom));display:flex;padding-left:41px}
.nav a{color:#fff;text-decoration:none;font-size:13.5px;font-weight:600;line-height:43px;padding:0 20px}
.nav a.active{background:var(--nav-active)}

.hero{position:absolute;top:133px;left:0;width:963px;height:333px;border-bottom:1px solid var(--line)}
.hero-photo{position:absolute;left:365px;top:0;width:598px;height:333px;background:linear-gradient(90deg,#fff 0%,#eef0f2 18%,#e4e3df 50%,#eceef0 80%,#f4f1de 100%)}
.hero-text{position:absolute;left:61px;top:70px;width:330px}
.hero-text h1{font-size:35px;font-weight:400;color:var(--brand);white-space:nowrap;line-height:1.1}
.hero-text h2{font-size:24px;font-weight:400;color:var(--blue);margin:6px 0 0 5px}
.hero-text p{font-size:11px;line-height:18px;margin:8px 0 0 5px;color:#777}
.dots{display:flex;gap:3px;margin:10px 0 0 5px}
.dots span{width:12px;height:12px;border-radius:50%;background:#eee}
.dots span:first-child{background:#ccc}

.packages-title{position:absolute;top:495px;left:0;width:963px;text-align:center;font-size:29px;font-weight:300;color:var(--heading)}
.card{position:absolute;top:549px;width:272px;height:198px;border:1px solid #d6d6d6;border-radius:6px;background:linear-gradient(#fff,#f3f3f3);text-align:center;padding-top:24px}
.card h3{font-size:23px;font-weight:600;line-height:1}
.card p{font-size:10.5px;line-height:17px;color:#888;margin:8px 18px 0}
.price{font-size:29px;font-weight:700;margin-top:8px;line-height:1}
.price small{font-size:20px}
.pay{display:inline-block;margin-top:10px;width:64px;height:31px;border:1px solid #cfcfcf;border-radius:3px;background:#fff;font-size:12px;font-weight:400;color:var(--text);line-height:29px}
.silver{left:58px}.gold{left:345px}.diamond{left:631px}
.silver h3,.silver .price,.gold .price{color:var(--blue)}
.gold h3{color:#1e5a97}
.diamond h3{color:var(--diamond)}
.diamond .price{color:var(--orange)}

.divider{position:absolute;top:783px;left:0;width:963px;height:1px;background:var(--line)}

.about{position:absolute;top:817px;left:45px;width:270px}
.about h2{font-size:24px;font-weight:300;color:var(--heading)}
.about p{font-size:10.5px;line-height:19px;text-align:justify;margin-top:9px;color:#666}
.about p+p{margin-top:15px}

.calendar{position:absolute;top:817px;left:363px}
.calendar h2{font-size:24px;font-weight:400;color:var(--blue)}
.cal{margin-top:10px;width:224px;border-collapse:collapse;font-size:12.5px;text-align:center}
.cal caption{background:var(--cal-head);color:#fff;font-size:14px;height:28px;line-height:28px;border-radius:3px 3px 0 0;position:relative}
.cal caption .prev,.cal caption .next{position:absolute;top:0;font-size:9px}
.cal caption .prev{left:10px}.cal caption .next{right:10px}
.cal th{background:var(--cal-days);color:#fff;font-weight:600;font-size:11px;height:22px}
.cal td{border:1px solid #ddd;height:25px;color:#333}
.cal td.muted{color:#aaa}
.cal td.today{background:#222;color:#fff}

.video{position:absolute;top:825px;left:621px;width:298px;height:240px;border:1px solid #ddd;border-radius:6px;box-shadow:0 0 4px rgba(0,0,0,.08)}
.video-frame{position:absolute;left:14px;top:12px;width:270px;height:172px;border-radius:6px;background:linear-gradient(120deg,#f4f7fa,#cfe3ee 55%,#8cc6d8)}
.play{position:absolute;left:112px;top:63px}
.video h3{position:absolute;left:22px;top:193px;font-size:17px;font-weight:600;color:var(--blue)}
.video p{position:absolute;left:22px;top:218px;font-size:10.5px;color:#888}

.footer{position:absolute;top:1105px;left:0;width:963px;height:95px;background:var(--footer);color:#fff;padding:21px 0 0 49px}
.footer nav{font-size:13px}
.footer nav a{color:#fff;text-decoration:none}
.footer nav .sep{margin:0 7px}
.footer small{display:block;font-size:10px;margin-top:10px}
</style>
</head>
<body>
<div class="topline"></div>

<div class="logo"><span class="logo-mark"></span><span class="logo-name">TOVAR</span></div>
<div class="logo-sub">Online Tuition</div>

<div class="social"><span>friendbook</span><span>chirpnet</span><span>voxly</span></div>
<div class="enroll">Enroll here</div>
<div class="login">
  <div class="field">Username</div>
  <div class="field">Password</div>
  <div class="btn">Login</div>
</div>

<nav class="nav">
  <a class="active">Home</a><a>Turtorial Packages</a><a>Weekly Tips</a><a>Reading</a><a>Speaking</a><a>Listening</a><a>Writing</a><a>Video</a><a>Contact</a>
</nav>

<section class="hero">
  <div class="hero-photo" role="img" aria-label="Photo of a smiling tutor seated in a bright office with shelves and flowers"></div>
  <div class="hero-text">
    <h1>We Teaching Your Online</h1>
    <h2>Mauris vel lacus vitae felis</h2>
    <p>Etiam est nunc, venenatis in, tristique eu, imperdiet ac, nisl. Cum sociis natoque penatibus et magnis dis parturient montes, nascetur ridiculus mus.</p>
    <div class="dots"><span></span><span></span><span></span></div>
  </div>
</section>

<h2 class="packages-title">Our Packages of Online tuition</h2>
<div class="card silver">
  <h3>SILVER</h3>
  <p>Mauris vel lacus vitae felis vestibulum volutpat Etiam est nunc venenatis in tristique eu imperdiet ac nisl Cum sociis</p>
  <div class="price">$24<small>.99</small></div>
  <span class="pay">paywick</span>
</div>
<div class="card gold">
  <h3>GOLD</h3>
  <p>Mauris vel lacus vitae felis vestibulum volutpat Etiam est nunc venenatis in tristique eu imperdiet ac nisl Cum sociis</p>
  <div class="price">$39<small>.99</small></div>
  <span class="pay">paywick</span>
</div>
<div class="card diamond">
  <h3>DIAMOND</h3>
  <p>Mauris vel lacus vitae felis vestibulum volutpat Etiam est nunc venenatis in tristique eu imperdiet ac nisl Cum sociis</p>
  <div class="price">$49<small>.99</small></div>
  <span class="pay">paywick</span>
</div>

<div class="divider"></div>

<section class="about">
  <h2>About Our Institute</h2>
  <p>Mauris vel lacus vitae felis vestibulum volutpat. Etiam est nunc, venenatis in, tristique eu, imperdiet ac, nisl. Cum sociis natoque penatibus et magnis dis parturient montes, nascetur ridiculus mus. In iaculis facilisis massa. Etiam eu urna. Sed porta.</p>
  <p>Suspendisse quam leo, molestie sed, luctus quis, feugiat in, pede. Fusce tellus. Sed metus augue, convallis et, vehicula ut, pulvinar eu, ante. Integer orci tellus, tristique vitae, consequat nec, porta vel, lectus. Nulla sit amet diam. Duis non nunc</p>
</section>

<section class="calendar">
  <h2>Our Calender</h2>
  <table class="cal">
    <caption><span class="prev">&#9664;</span>January 2013<span class="next">&#9654;</span></caption>
    <tr><th>Su</th><th>Mo</th><th>Tu</th><th>We</th><th>Th</th><th>Fr</th><th>Sa</th></tr>
    <tr><td class="muted">28</td><td class="muted">29</td><td class="muted">30</td><td class="muted">31</td><td>1</td><td>2</td><td>3</td></tr>
    <tr><td>4</td><td>5</td><td>6</td><td>7</td><td>8</td><td>9</td><td>10</td></tr>
    <tr><td>11</td><td>12</td><td>13</td><td>14</td><td>15</td><td>16</td><td>17</td></tr>
    <tr><td>18</td><td>19</td><td class="today">20</td><td>21</td><td>22</td><td>23</td><td>24</td></tr>
    <tr><td>25</td><td>26</td><td>27</td><td>28</td><td>29</td><td>30</td><td class="muted">1</td></tr>
    <tr><td class="muted">2</td><td class="muted">3</td><td class="muted">4</td><td class="muted">5</td><td class="muted">6</td><td class="muted">7</td><td class="muted">8</td></tr>
  </table>
</section>

<section class="video">
  <div class="video-frame" role="img" aria-label="Video still of hands typing on a laptop keyboard">
    <svg class="play" width="46" height="46" viewBox="0 0 46 46"><circle cx="23" cy="23" r="23" fill="#fff" fill-opacity=".85"/><path d="M18 13 L33 23 L18 33 Z" fill="#111"/></svg>
  </div>
  <h3>Watch Our latest Video</h3>
  <p>In iaculis facilisis massa Etiam eu urna Sed porta.</p>
</section>

<footer class="footer">
  <nav><a>Home</a><span class="sep">|</span><a>Turtorial Packages</a><span class="sep">|</span><a>Weekly Tips</a><span class="sep">|</span><a>Reading</a><span class="sep">|</span><a>Speaking</a><span class="sep">|</span><a>Listening</a><span class="sep">|</span><a>Writing</a><span class="sep">|</span><a>Contact</a></nav>
  <small>© 2013 Company Name. All right reserved. &nbsp;Term of Use</small>
</footer>
</body>
</html>
```